Brivane Management

We need a web design for a new consulting company, with clients all over the world. The company provides management consulting to the travel industry.

Logo files are attached.

Website must look very corporate and be responsive in design.

Management Consulting

```html
<!DOCTYPE html>
<html lang="en">
<head>
<meta charset="utf-8">
<title>Brivane Management</title>
<link rel="stylesheet" href="https://fonts.googleapis.com/css2?family=Cinzel:wght@400;700&family=Lato:ital,wght@0,400;0,700;1,400&family=Oswald:wght@500&display=swap">
<style>
:root{
  --navy:#13225a;
  --blue:#1a6fb5;
  --green:#4b9a1a;
  --green-dark:#3a7e10;
  --text:#333;
  --muted:#555;
  --band:#f1f1f1;
  --footer:#333333;
  --footer-deep:#232323;
  --line:#d8d8d8;
}
*{box-sizing:border-box;margin:0;padding:0}
html,body{width:797px;height:1200px;overflow:hidden;background:#fff}
body{position:relative;font-family:"Lato",sans-serif;color:var(--text);font-size:9px}

/* header */
.site-header{position:absolute;left:0;top:0;width:797px;height:52px;background:linear-gradient(#fff,#eee);border-top:2px solid var(--green);border-bottom:1px solid #ddd}
.brand{position:absolute;left:88px;top:12px;display:flex;align-items:center;gap:7px}
.brand-mark{width:26px;height:26px;border-radius:50%;background:var(--navy)}
.brand-name{font-family:"Cinzel",serif;font-size:21px;color:var(--navy);font-weight:700}
.main-nav{position:absolute;left:397px;top:0;display:flex;height:50px}
.main-nav a{width:72px;height:50px;border-left:1px solid #d4d4d4;display:flex;flex-direction:column;align-items:center;justify-content:flex-end;padding-bottom:5px;text-decoration:none;color:#222;font-size:12px;gap:6px}
.main-nav a:last-child{border-right:1px solid #d4d4d4}
.main-nav a.active{color:var(--blue);background:#f7f7f7}
.main-nav svg{width:18px;height:18px}

/* hero */
.hero{position:absolute;left:0;top:52px;width:797px;height:293px;background:linear-gradient(100deg,#9bb0c4 0%,#e7e2dc 30%,#d7d3cf 50%,#3a4150 75%,#c8d2db 100%)}
.hero-arrow{position:absolute;top:141px;width:24px;height:22px;background:#3a3a3a;display:flex;align-items:center;justify-content:center}
.hero-caption{position:absolute;left:88px;top:198px;width:262px;height:50px;background:rgba(30,35,60,.72);border-left:4px solid #8fa0c8;padding:4px 8px;font-family:"Oswald",sans-serif;color:#fff;font-size:15px;line-height:21px}
.hero-dots{position:absolute;left:368px;top:274px;display:flex;gap:5px}
.hero-dots span{width:10px;height:10px;background:#fff;border:1px solid #bbb}
.hero-dots span.on{background:var(--green)}

/* welcome */
.welcome{position:absolute;left:0;top:345px;width:797px;height:163px;text-align:center}
.welcome-title{position:absolute;left:0;width:797px;top:22px;display:flex;justify-content:center;align-items:center;gap:8px;font-family:"Cinzel",serif;font-size:20px;color:#222}
.welcome-title .brand-mark{width:28px;height:28px}
.welcome-title .accent{color:var(--navy)}
.welcome-lead{position:absolute;top:59px;width:797px;font-style:italic;color:var(--navy);font-size:9.5px}
.welcome-body{position:absolute;top:80px;left:88px;width:616px;font-size:8.5px;line-height:14px;color:var(--muted)}
.btn{display:inline-block;background:linear-gradient(#5aad25,var(--green-dark));color:#fff;font-weight:700;text-decoration:none;border-radius:2px}
.welcome .btn{position:absolute;left:364px;top:128px;width:63px;height:22px;line-height:22px;font-size:9px}

/* services */
.services{position:absolute;left:0;top:508px;width:797px;height:229px;background:var(--band)}
.service-card{position:absolute;top:35px;width:142px;height:175px;background:#fff;border:1px solid #ddd;padding:10px}
.service-badge{position:absolute;left:53px;top:-19px;width:36px;height:36px;border-radius:50%;background:var(--navy);border:3px solid #d6d9e6}
.service-photo{width:120px;height:82px;background:linear-gradient(135deg,#c9d3de,#7d8ea3)}
.service-card h3{font-family:"Cinzel",serif;font-weight:400;font-size:13px;color:#222;margin:5px 0 2px;letter-spacing:.5px}
.service-card p{font-size:8.5px;line-height:12px;color:#444}
.service-card .btn{margin-top:5px;width:44px;height:17px;line-height:17px;text-align:center;font-size:8.5px;font-weight:400}

/* info columns */
.col{position:absolute;top:755px}
.col h4{font-family:"Cinzel",serif;font-weight:400;font-size:14px;color:#222;border-bottom:1px solid var(--line);padding-bottom:4px;position:relative;letter-spacing:.5px}
.col h4:after{content:"";position:absolute;left:0;bottom:-1px;width:42px;height:2px;background:var(--blue)}
.checks{list-style:none;margin-top:5px}
.checks li{display:flex;gap:6px;align-items:center;font-size:8.5px;color:#444;height:16.7px}
.checks li i{width:9px;height:9px;border-radius:50%;background:#222;display:flex;align-items:center;justify-content:center}
.more-link{position:absolute;top:118px;color:var(--green);font-size:8.5px;font-weight:700;text-decoration:none}
.news{margin-top:9px;font-size:8.5px;line-height:11px;color:#555}
.news b{display:block;font-weight:400;color:#222}
.news div{margin-bottom:7px}
.experts{display:flex;gap:5px;margin-top:10px}
.expert{width:71px}
.expert-photo{height:58px;background:linear-gradient(#c6ccd4,#9aa4b1);border:1px solid #ccc}
.expert span{display:block;background:var(--navy);color:#fff;font-size:8px;text-align:center;height:13px;line-height:13px}

/* testimonials */
.testimonials{position:absolute;left:0;top:903px;width:797px;height:132px;background:var(--band);border-bottom:3px solid var(--blue)}
.testimonials h2{position:absolute;top:14px;width:797px;text-align:center;font-family:"Cinzel",serif;font-weight:400;font-size:15px;color:#222;letter-spacing:1px}
.testimonials h2:before,.testimonials h2:after{content:"";position:absolute;top:10px;width:150px;height:1px;background:#ccc}
.testimonials h2:before{left:145px}.testimonials h2:after{right:145px}
.client-photo{position:absolute;left:89px;top:44px;width:57px;height:57px;border-radius:50%;background:linear-gradient(#e8d9c8,#c9b8a5);border:2px solid var(--navy)}
.quote{position:absolute;left:172px;top:46px;width:532px;font-style:italic;font-size:8.5px;line-height:14px;color:#444;border-bottom:1px solid #ddd;padding-bottom:4px}
.quote-by{position:absolute;left:171px;top:98px;font-weight:700;font-size:8.5px;color:#333}

/* footer */
.site-footer{position:absolute;left:0;top:1038px;width:797px;height:128px;background:var(--footer);color:#ddd}
.fcol{position:absolute;top:9px}
.fcol h5{font-size:12px;font-weight:400;color:#fff;border-bottom:1px solid #4a4a4a;padding-bottom:4px;margin-bottom:6px}
.fcol ul{list-style:none}
.fcol li{font-size:8.5px;height:16.5px;display:flex;gap:6px;align-items:flex-start}
.contact li{height:auto;margin-bottom:10px;line-height:10px}
.contact svg{flex:none;width:10px;height:10px}
.news-input{width:137px;height:17px;background:#fff;color:#888;font-size:7px;padding:4px;margin-top:10px}
.site-footer .btn{margin-top:10px;font-size:9px;width:70px;height:19px;line-height:19px;text-align:center}
.socials{display:flex;gap:8px;margin-top:2px}
.socials span{width:19px;height:19px;border-radius:50%;background:#555}
.socials span.hl{background:#1f8fd6}
.footer-brand{position:absolute;left:0;top:56px;display:flex;gap:5px;align-items:center;font-size:15px;font-weight:700;color:#fff;white-space:nowrap}
.footer-brand i{width:20px;height:20px;border-radius:50%;background:#fff}
.copyright{position:absolute;left:0;top:1166px;width:797px;height:34px;background:var(--footer-deep);color:#eee;text-align:center;line-height:28px;font-size:8.5px}
</style>
</head>
<body>

<header class="site-header">
  <div class="brand"><span class="brand-mark"></span><span class="brand-name">BRIVANE</span></div>
  <nav class="main-nav">
    <a href="#" class="active"><svg viewBox="0 0 20 20"><path d="M2 10 10 3l8 7h-3v7h-4v-5H9v5H5v-7z" fill="#1a6fb5"/></svg>Home</a>
    <a href="#"><svg viewBox="0 0 20 20"><circle cx="7" cy="6" r="3.2" fill="#13225a"/><circle cx="13.5" cy="6" r="3.2" fill="#13225a"/><path d="M1 17c0-4 3-6 6-6s6 2 6 6zM11 17c0-3 0-5 2.5-6 3 0 5.5 2 5.5 6z" fill="#13225a"/></svg>About Us</a>
    <a href="#"><svg viewBox="0 0 20 20"><circle cx="8" cy="9" r="5" fill="none" stroke="#13225a" stroke-width="3" stroke-dasharray="2.5 1.4"/><circle cx="15" cy="15" r="3" fill="none" stroke="#13225a" stroke-width="2"/></svg>Services</a>
    <a href="#"><svg viewBox="0 0 20 20"><rect x="3" y="2" width="12" height="16" fill="none" stroke="#13225a" stroke-width="1.6"/><path d="M6 7h6M6 10h6M6 13h3M11 15l6-7" stroke="#13225a" stroke-width="1.6"/></svg>Contact</a>
  </nav>
</header>

<section class="hero" role="img" aria-label="Photo of consultants smiling around a meeting table">
  <span class="hero-arrow" style="left:4px"><svg width="8" height="10" viewBox="0 0 8 10"><path d="M6 1 2 5l4 4" stroke="#fff" stroke-width="2" fill="none"/></svg></span>
  <span class="hero-arrow" style="right:4px"><svg width="8" height="10" viewBox="0 0 8 10"><path d="M2 1l4 4-4 4" stroke="#fff" stroke-width="2" fill="none"/></svg></span>
  <div class="hero-caption">WE PROVIDES MANAGEMENT<br>CONSULTING TO THE TRAVEL INDUSTRY.</div>
  <div class="hero-dots"><span></span><span class="on"></span><span></span><span></span></div>
</section>

<section class="welcome">
  <div class="welcome-title"><span class="brand-mark"></span>WELCOME TO <span class="accent">BRIVANE</span></div>
  <p class="welcome-lead">Lorem ipsum dolor sit amet, consectetur adipiscing eli Vestibulum efficitur pellentesque mi, ut vestibulum mauris sagittis at.</p>
  <p class="welcome-body">Aliquam vitae magna aliquet, molestie est eget, ultricies arcu. Nunc non luctus turpis, et sollicitudin sem. In at vehicula tellus. Nulla vel eleifend nulla, quis ultrices metus. Nunc finibus nisi ac congue tempor. Nulla elementum, leo non vehicula lacinia, velit libero hendrerit purus, sed feugiat felis orci id erat. Cras ultrices vehicula lectus a porttitor. Nunc eu enim at sem varius aliquet Vestibulum eu dolor erat. Aenean luctus venenatis</p>
  <a href="#" class="btn">Read More</a>
</section>

<section class="services">
  <article class="service-card" style="left:87px"><span class="service-badge"></span><div class="service-photo" role="img" aria-label="Team working on laptops"></div><h3>CONSULTING</h3><p>Lorem ipsum dolor consectetur adipiscing elit estibueff</p><a href="#" class="btn">MORE</a></article>
  <article class="service-card" style="left:245px"><span class="service-badge"></span><div class="service-photo" role="img" aria-label="Colleagues reviewing documents"></div><h3>ANALYSIS</h3><p>Lorem ipsum dolor consectetur adipiscing elit estibueff</p><a href="#" class="btn">MORE</a></article>
  <article class="service-card" style="left:403px"><span class="service-badge"></span><div class="service-photo" role="img" aria-label="Hands pointing at a tablet chart"></div><h3>SERVICES</h3><p>Lorem ipsum dolor consectetur adipiscing elit estibueff</p><a href="#" class="btn">MORE</a></article>
  <article class="service-card" style="left:562px"><span class="service-badge"></span><div class="service-photo" role="img" aria-label="Business meeting with charts"></div><h3>STRATEGY</h3><p>Lorem ipsum dolor consectetur adipiscing elit estibueff</p><a href="#" class="btn">MORE</a></article>
</section>

<section class="col" style="left:87px;width:161px">
  <h4>OUR CAPABILITIES</h4>
  <ul class="checks">
    <li><i><svg width="6" height="6" viewBox="0 0 6 6"><path d="M1 3l1.4 1.4L5 1.6" stroke="#fff" fill="none"/></svg></i>At vero eos et accusamus et iusto</li>
    <li><i><svg width="6" height="6" viewBox="0 0 6 6"><path d="M1 3l1.4 1.4L5 1.6" stroke="#fff" fill="none"/></svg></i>Dignissimos ducimus qui blanditiis</li>
    <li><i><svg width="6" height="6" viewBox="0 0 6 6"><path d="M1 3l1.4 1.4L5 1.6" stroke="#fff" fill="none"/></svg></i>Daesentium voluptatum deleniti atque</li>
    <li><i><svg width="6" height="6" viewBox="0 0 6 6"><path d="M1 3l1.4 1.4L5 1.6" stroke="#fff" fill="none"/></svg></i>Corrupti quos dolores et quas</li>
    <li><i><svg width="6" height="6" viewBox="0 0 6 6"><path d="M1 3l1.4 1.4L5 1.6" stroke="#fff" fill="none"/></svg></i>Alestias excepturi sint occaecati cup</li>
  </ul>
  <a href="#" class="more-link">View More →</a>
</section>

<section class="col" style="left:300px;width:128px">
  <h4>WHAT’S NEW?</h4>
  <div class="news">
    <div><b>March 14, 2013</b>Lorem ipsum dolor sit amet, consectetur adipiscing elit. Sed...</div>
    <div><b>February 20, 2013</b>Lorem ipsum dolor sit amet, consectetur adipiscing elit. Sed...</div>
  </div>
  <a href="#" class="more-link">Archive →</a>
</section>

<section class="col" style="left:480px;width:224px">
  <h4>OUR LEADING EXPERTS</h4>
  <div class="experts">
    <div class="expert"><div class="expert-photo" role="img" aria-label="Portrait of Nora Halvik"></div><span>Nora Halvik</span></div>
    <div class="expert"><div class="expert-photo" role="img" aria-label="Portrait of Ella Dorsan"></div><span>Ella Dorsan</span></div>
    <div class="expert"><div class="expert-photo" role="img" aria-label="Portrait of Tom Reyvel"></div><span>Tom Reyvel</span></div>
  </div>
  <a href="#" class="more-link">Explore →</a>
</section>

<section class="testimonials">
  <h2>CLIENT TESTIMONIALS</h2>
  <div class="client-photo" role="img" aria-label="Portrait of the client"></div>
  <p class="quote">“ Lorem ipsdolor sit amet, consectetur adipiscing elit. Donec sit amet nulla vitae tortor iaculis commodo. Nulla interdum dui vitae lectus malesuada ac dignissim mi vehicula. Nullam ornare vulputate sem vitae convallis. Proin et faucibus eros. Nam id rutrum risus, quis eleifend tortor. Nulla scelerisque vitae ante vitae, rhoncus pellentesque turpis. Donec feugiat malesuada justo, quis porta urna egestas nec. Duis nec lobortis justo, ac varius ante. ”</p>
  <p class="quote-by">Mr. Owen Tasler</p>
</section>

<footer class="site-footer">
  <div class="fcol" style="left:86px;width:66px">
    <h5>Quick Links</h5>
    <ul><li>›&nbsp; Home</li><li>›&nbsp; About Us</li><li>›&nbsp; Services</li><li>›&nbsp; Contact Us</li></ul>
  </div>
  <div class="fcol contact" style="left:203px;width:152px">
    <h5>Contact Information</h5>
    <ul>
      <li><svg viewBox="0 0 10 10"><path d="M5 0a3.4 3.4 0 0 0-3.4 3.4C1.6 6 5 10 5 10s3.4-4 3.4-6.6A3.4 3.4 0 0 0 5 0z" fill="#fff"/></svg>Lorem ipsum dolor consectetuer adipiscing elit, Larkfield Row, unit 7, 00000</li>
      <li><svg viewBox="0 0 10 10"><path d="M2 0 4 2.5 3 4a6 6 0 0 0 3 3l1.5-1L10 8l-1.5 2C4 10 0 6 0 1.5z" fill="#fff"/></svg>+00 555 0100</li>
      <li><svg viewBox="0 0 10 10"><rect y="2" width="10" height="7" fill="#fff"/><path d="M0 2l5 4 5-4" stroke="#333" fill="none"/></svg>hello@brivane-example.com</li>
    </ul>
  </div>
  <div class="fcol" style="left:410px;width:137px">
    <h5>Newsletter Sign Up</h5>
    <p style="font-size:8px;line-height:11px">Lorem ipsudolor sit coec adipiscing elitsite amet</p>
    <div class="news-input">Email Address</div>
    <a href="#" class="btn">SUBSCRIBE</a>
  </div>
  <div class="fcol" style="left:600px;width:104px">
    <h5>Follow Us</h5>
    <div class="socials" aria-label="Social links"><span></span><span class="hl"></span><span></span><span></span></div>
    <div class="footer-brand"><i></i>BRIVANE</div>
  </div>
</footer>
<div class="copyright">Copyright © 2014 - brivane-example.com</div>

</body>
</html>
```